Design a web site for my business - Brightline Coatings Co.

We are a family business that handles design, fabrication and installation of powder coated aluminum, stainless steel and glass products. Including handrails, privacy slat screens, electric gates and pool fencing. We are based in the Whitsundays in North Queensland and service an area from Airlie Beach to Townsville.

Target Market(s)

Domestic and commercial

Industry/Entity Type

fabrication - manufacturing

Coding

Coded - Design and coding required

Number of Pages Required

5+ page

Colors
0054AA
0677BA
7BADD7
CADEEF
E8F1F8

Requirements
Must have
• photo galleries, contact page, one page for privacy screens, balustrades, glass fencing, stainless steel handrail, powder coated aluminium handrails and pool fencing

```html
<!DOCTYPE html>
<html lang="en">
<head>
<meta charset="utf-8">
<title>Brightline Coatings Co</title>
<link rel="stylesheet" href="https://fonts.googleapis.com/css2?family=Exo+2:ital,wght@0,600;0,700;0,800;1,800&family=Open+Sans:wght@400;600;700&display=swap">
<style>
:root{
  --navy:#34506e;
  --navy-band:#3a5674;
  --sage:#4f6a62;
  --footer:#4e665f;
  --ink:#1f2428;
  --body:#3b4045;
  --white:#ffffff;
  --muted:#9fb0c2;
}
*{box-sizing:border-box;margin:0;padding:0}
html,body{width:1200px;height:4781px;overflow:hidden;background:var(--white)}
body{position:relative;font-family:"Open Sans",sans-serif;color:var(--body)}
.abs{position:absolute}
.btn{position:absolute;display:flex;align-items:center;justify-content:center;border-radius:30px;background:var(--sage);color:var(--white);font:700 13px "Open Sans",sans-serif;letter-spacing:.6px;text-transform:uppercase}
.section-title{position:absolute;font:700 48px/1 "Exo 2",sans-serif;color:var(--ink);letter-spacing:.5px}
.title-rule{position:absolute;width:70px;height:6px}
.brand{position:absolute;display:flex;align-items:center;gap:10px;color:var(--white);font:700 16px "Exo 2",sans-serif;letter-spacing:.8px;text-transform:uppercase}
.brand .dot{width:14px;height:14px;border-radius:50%;background:var(--white)}

/* hero */
.hero{position:absolute;left:0;top:0;width:1200px;height:640px;background:linear-gradient(160deg,#1b2b63 0%,#253a6e 35%,#3c4a62 60%,#2a2d33 100%)}
.nav{position:absolute;left:525px;top:57px;display:flex;gap:28px;font-size:15px;color:#d9e0ea}
.nav .active{color:var(--white);font-weight:600}
.hero h1{position:absolute;left:113px;top:256px;width:560px;font:800 50px/53px "Exo 2",sans-serif;color:var(--white);text-transform:uppercase;letter-spacing:.3px}

/* about */
.about-frame{position:absolute;left:95px;top:751px;width:185px;height:140px;border-left:18px solid var(--navy);border-top:14px solid var(--navy)}
.photo{position:absolute}
.about-text{position:absolute;left:690px;top:900px;width:395px}
.about-text .lead{font-size:16px;color:var(--ink);margin-bottom:12px}
.about-text p{font-size:13.5px;line-height:24px;margin-bottom:10px}

/* services */
.services{position:absolute;left:0;top:1419px;width:1200px;height:748px;background:var(--navy-band)}
.services .section-title{color:var(--white)}
.card{position:absolute;top:221px;height:421px;width:362px}
.card span{position:absolute;left:42px;bottom:50px;color:var(--white);font:600 20px/28px "Exo 2",sans-serif;text-transform:uppercase}

/* project */
.feature-card{position:absolute;left:657px;top:2623px;width:443px;height:365px;background:var(--white);box-shadow:0 10px 30px rgba(0,0,0,.12);padding:50px 50px 0 50px}
.feature-card h3{font:600 20px "Open Sans",sans-serif;color:var(--ink);margin-bottom:22px}
.feature-card p{font-size:13.5px;line-height:24px;margin-bottom:10px}

/* testimonial */
.quote-card{position:absolute;left:202px;top:3578px;width:794px;height:293px;background:var(--white);box-shadow:0 10px 30px rgba(0,0,0,.12);text-align:center}
.quote-card blockquote{position:absolute;left:60px;right:60px;top:112px;font-size:20px;line-height:34px;color:var(--ink)}
.quote-card cite{position:absolute;left:0;right:0;top:212px;font:400 19px "Open Sans",sans-serif;font-style:normal;color:var(--ink);text-transform:uppercase}

/* contact */
.contact h2{position:absolute;left:0;width:1200px;top:4030px;text-align:center;font:700 48px "Exo 2",sans-serif;color:var(--ink)}
.contact p{position:absolute;left:215px;width:770px;top:4130px;text-align:center;font-size:19px;line-height:34px;color:var(--ink)}

/* footer */
.footer{position:absolute;left:0;top:4428px;width:1200px;height:353px;background:var(--footer);color:var(--white)}
.footer .info{position:absolute;font-size:16px;line-height:27px}
.footer .rule{position:absolute;left:111px;top:193px;width:978px;height:1px;background:rgba(255,255,255,.45)}
.footer-nav{position:absolute;left:0;width:1200px;top:238px;display:flex;justify-content:center;gap:28px;font-size:15px}
.footer-nav .active{font-weight:700}
.copy{position:absolute;left:0;width:1200px;top:280px;text-align:center;font-size:14px}
</style>
</head>
<body>

<!-- Hero -->
<header class="hero" role="img" aria-label="Photo of a house with horizontal slat aluminium fencing under a blue sky">
  <div class="brand" style="left:111px;top:72px"><span class="dot"></span>Brightline Coatings Co</div>
  <nav class="nav"><span class="active">Home</span><span>About</span><span>Services</span><span>Projects</span><span>Contact</span></nav>
  <a class="btn" style="left:922px;top:41px;width:165px;height:52px">Get a quote</a>
  <h1>Custom aluminium, glass &amp; stainless steel solutions built to last</h1>
  <a class="btn" style="left:113px;top:486px;width:219px;height:52px;background:#3f5d80">Explore our work</a>
</header>

<!-- About -->
<div class="about-frame"></div>
<div class="photo" style="left:111px;top:764px;width:509px;height:538px;background:linear-gradient(180deg,#3a69b8 0%,#7aa3d8 40%,#6fa7a0 62%,#3f6a33 85%,#586046 100%)" role="img" aria-label="Photo of a modern home with pool and black pool fencing"></div>
<h2 class="section-title" style="left:690px;top:806px">ABOUT US</h2>
<svg class="title-rule" style="left:690px;top:863px" viewBox="0 0 70 6"><polygon points="0,2 70,2 35,6" fill="#4f6a62"/></svg>
<div class="about-text">
  <div class="lead">Craftsmanship You Can Trust</div>
  <p>At Brightline Coatings Co, quality craftsmanship and attention to detail are at the heart of everything we do. As a locally owned family business, we specialise in designing, manufacturing, and installing custom aluminium, stainless steel, and glass solutions that enhance both the appearance and functionality of your property.</p>
  <p>Whether you're upgrading your home's outdoor spaces or completing a large commercial project, our experienced team delivers durable, low-maintenance products built to withstand North Queensland's demanding climate.</p>
</div>
<a class="btn" style="left:683px;top:1208px;width:167px;height:55px">Learn more</a>

<!-- Services -->
<section class="services">
  <h2 class="section-title" style="left:109px;top:96px">OUR SERVICES</h2>
  <svg class="title-rule" style="left:109px;top:156px" viewBox="0 0 70 6"><polygon points="0,2 70,2 35,6" fill="#ffffff"/></svg>
  <svg class="abs" style="left:950px;top:112px" width="140" height="14" viewBox="0 0 140 14">
    <path d="M2 7H45M2 7l6-4M2 7l6 4" stroke="#9fb0c2" stroke-width="1.5" fill="none"/>
    <path d="M72 7H138M138 7l-6-4M138 7l-6 4" stroke="#ffffff" stroke-width="1.5" fill="none"/>
  </svg>
  <div class="card" style="left:111px;background:linear-gradient(180deg,#2c4c8a 0%,#6d7f92 40%,#a9b1b8 70%,#6b6f70 100%)" role="img" aria-label="Photo of powder coated aluminium louvre fencing"><span>Powder coated<br>aluminium</span></div>
  <div class="card" style="left:497px;background:linear-gradient(180deg,#d7d8d8 0%,#3a2f2a 35%,#a27860 65%,#4b3b32 100%)" role="img" aria-label="Photo of timber stairs with stainless wire handrail"><span>Handrails</span></div>
  <div class="card" style="left:883px;width:317px;background:linear-gradient(180deg,#4d4038 0%,#2f2620 45%,#6e6a5c 75%,#8a8b80 100%)" role="img" aria-label="Photo of stainless steel and glass balustrade on a house"><span>Stainless steel<br>&amp; glass</span></div>
</section>

<!-- Featured projects -->
<h2 class="section-title" style="left:111px;top:2310px">FEATURED PROJECTS</h2>
<svg class="title-rule" style="left:111px;top:2368px" viewBox="0 0 70 6"><polygon points="0,2 70,2 35,6" fill="#4f6a62"/></svg>
<svg class="abs" style="left:950px;top:2326px" width="140" height="14" viewBox="0 0 140 14">
  <path d="M2 7H45M2 7l6-4M2 7l6 4" stroke="#777" stroke-width="1.5" fill="none"/>
  <path d="M72 7H138M138 7l-6-4M138 7l-6 4" stroke="#1f2428" stroke-width="1.5" fill="none"/>
</svg>
<div class="abs" style="left:98px;top:2857px;width:190px;height:143px;border-left:14px solid var(--navy);border-bottom:12px solid var(--navy)"></div>
<div class="photo" style="left:111px;top:2436px;width:978px;height:552px;background:linear-gradient(100deg,#5d8ad0 0%,#d35b2a 22%,#3a3838 45%,#4a4a48 70%,#8aa046 100%)" role="img" aria-label="Photo of a balcony balustrade on an orange rendered building with palms"></div>
<div class="feature-card">
  <h3>BUILT WITH PRECISION.</h3>
  <p>Lorem ipsum dolor sit amet, consectetur adipiscing elit, sed do eiusmod tempor incididunt ut labore et dolore magna aliqua. Quis ipsum sus pendisse ultrices gsus commodo vive.</p>
  <p>Quis ipsum sus pendisse ultrices gravida.</p>
</div>
<a class="btn" style="left:703px;top:2888px;width:167px;height:54px">Learn more</a>

<!-- Happy clients -->
<h2 class="section-title" style="left:111px;top:3137px">HAPPY CLIENTS</h2>
<svg class="title-rule" style="left:111px;top:3195px" viewBox="0 0 70 6"><polygon points="0,2 70,2 35,6" fill="#4f6a62"/></svg>
<svg class="abs" style="left:950px;top:3153px" width="140" height="14" viewBox="0 0 140 14">
  <path d="M2 7H45M2 7l6-4M2 7l6 4" stroke="#777" stroke-width="1.5" fill="none"/>
  <path d="M72 7H138M138 7l-6-4M138 7l-6 4" stroke="#1f2428" stroke-width="1.5" fill="none"/>
</svg>
<div class="abs" style="left:825px;top:3800px;width:188px;height:86px;background:var(--navy)"></div>
<div class="photo" style="left:111px;top:3263px;width:978px;height:553px;background:linear-gradient(180deg,#4b4a48 0%,#6d3d33 30%,#7a4538 55%,#b9b6ae 80%,#dadad6 100%)" role="img" aria-label="Photo of timber-look aluminium slat driveway gates"></div>
<div class="quote-card">
  <svg class="abs" style="left:30px;top:26px" width="82" height="60" viewBox="0 0 82 60">
    <path d="M36 4C18 8 4 20 4 40c0 10 6 16 14 16 9 0 15-6 15-14 0-8-6-13-13-13 2-8 8-14 17-17z" fill="#d4d6d8"/>
    <path d="M78 4C60 8 46 20 46 40c0 10 6 16 14 16 9 0 15-6 15-14 0-8-6-13-13-13 2-8 8-14 17-17z" fill="#d4d6d8"/>
  </svg>
  <svg class="abs" style="left:341px;top:66px" width="112" height="20" viewBox="0 0 112 20">
    <g fill="#4f6a62">
      <polygon points="10,1 12.6,7.2 19,7.6 14,11.8 15.6,18.4 10,14.8 4.4,18.4 6,11.8 1,7.6 7.4,7.2"/>
      <polygon transform="translate(23 0)" points="10,1 12.6,7.2 19,7.6 14,11.8 15.6,18.4 10,14.8 4.4,18.4 6,11.8 1,7.6 7.4,7.2"/>
      <polygon transform="translate(46 0)" points="10,1 12.6,7.2 19,7.6 14,11.8 15.6,18.4 10,14.8 4.4,18.4 6,11.8 1,7.6 7.4,7.2"/>
      <polygon transform="translate(69 0)" points="10,1 12.6,7.2 19,7.6 14,11.8 15.6,18.4 10,14.8 4.4,18.4 6,11.8 1,7.6 7.4,7.2"/>
      <polygon transform="translate(92 0)" points="10,1 12.6,7.2 19,7.6 14,11.8 15.6,18.4 10,14.8 4.4,18.4 6,11.8 1,7.6 7.4,7.2"/>
    </g>
  </svg>
  <blockquote>"Professional from start to finish. The quality of workmanship exceeded our expectations and the finished product looks fantastic."</blockquote>
  <cite>Sam Carter</cite>
</div>

<!-- Contact -->
<section class="contact">
  <h2>GET IN TOUCH</h2>
  <svg class="title-rule" style="left:565px;top:4097px" viewBox="0 0 70 6"><polygon points="0,2 70,2 35,6" fill="#4f6a62"/></svg>
  <p>Whether you need stylish pool fencing, custom gates, handrails, or architectural aluminium solutions, our experienced team is ready to help bring your vision to life.</p>
  <a class="btn" style="left:517px;top:4252px;width:166px;height:52px">Contact us</a>
</section>

<!-- Footer -->
<footer class="footer">
  <div class="brand" style="left:111px;top:75px;font-size:15px"><span class="dot"></span>Brightline Coatings Co</div>
  <svg class="abs" style="left:436px;top:88px" width="32" height="46" viewBox="0 0 32 46">
    <path d="M16 2C8 2 2 8 2 16c0 11 14 27 14 27s14-16 14-27C30 8 24 2 16 2z" fill="none" stroke="#fff" stroke-width="2"/>
    <circle cx="16" cy="16" r="5" fill="none" stroke="#fff" stroke-width="2"/>
  </svg>
  <div class="info" style="left:479px;top:84px">12 Harbourview Road,<br>Seaford Bay, QLD, Australia, 4899</div>
  <svg class="abs" style="left:818px;top:92px" width="50" height="40" viewBox="0 0 50 40">
    <rect x="10" y="6" width="36" height="26" rx="3" fill="none" stroke="#fff" stroke-width="2"/>
    <path d="M10 8l18 14 18-14" fill="none" stroke="#fff" stroke-width="2"/>
    <path d="M3 14c0 10 6 20 18 22" fill="none" stroke="#fff" stroke-width="2"/>
  </svg>
  <div class="info" style="left:881px;top:84px">hello@brightlinecoatings.example<br>+61 400 000 123</div>
  <div class="rule"></div>
  <nav class="footer-nav"><span class="active">Home</span><span>About</span><span>Services</span><span>Projects</span><span>Contact</span></nav>
  <div class="copy">2026 Brightline Coatings Co. Al Rights Reserved.</div>
</footer>

</body>
</html>
```